Wine Label Logo NEW name too

We would like to see this done in more colors but, lighter ones too. the dark colors don't show up that well. Can you also do some on white wine and not just red wine?

Also, we aren't sure we will use the name Plumvale and wonder if you could use the name Honeyfrost with the same design to see how that looks, as well?

new wine label for a brand called Plumvale (one word) and is targeted to go after 21-40 year olds. Probably more women than men. There will be Plumvale Red, Plumvale White, Plumvale Cabernet, etc. the profile of the wine will be sweet...duh!!

would love you to come up with some TAG LINE ideas, as well. Size should be between 2 1/2 to 3 inches wide and 5 to 6 inches long. Needs place holders for varietal, Cabernet. 13.5% alcohol, area wil be California. I suggest you look at a bunch of wine labels to better understand this brief.

The final design should communicate fun, sweet, wine, young, hip

Wine labels matter. Period. Now, attempting to define “fun and contemporary” is nigh on impossible, but I think it would be safe to assume that this could mean “non-traditional.” Let’s face it. Design matters to millennial consumers. Quill, Tern Lodges, Loftly Journal – these brands are not ONLY for millennials by any means (well, maybe Tern), but design is top priority for these brands, and these brands have top priority for millennials. Feel free to do the math. If we spend money on something, we expect it to be beautiful and often times we expect social purchases like wine to act as a public reflection of our tastes and personality. This latter expectation is no different than any other generation (if arguably more intense due to our intrinsic personal branding tendencies); however, our personalities and what we are reflecting out to our peers IS different.
Updates

What about a label that is 2 1/2 to 3 inches wide and 5-6 inches long and looks like a white or off white piece of paper that has had berries poured across it with some stains and the name Plumvale Cabernet as the logo on the label?  Needs space for the AVA area grown to say California and the vintage 2011 and alcohol level in small letters 12.3%. 

Look at some wine labels to get a unique idea. Needs to appeal to 21-40 year old women. Needs to denote the wine is sweet

Reason: two partners are out of the country and I want them involved in the choice

Target Market(s)

Industry/Entity Type

Social

Logo Text

Plumvale Cabernet

Logo styles of interest
Pictorial/Combination Logo
Abstract Logo
Wordmark Logo

```html
<!DOCTYPE html>
<html lang="en">
<head>
<meta charset="utf-8">
<title>Plumvale Cabernet – Wine Label</title>
<link href="https://fonts.googleapis.com/css2?family=Playfair+Display:wght@400;500&family=Parisienne&display=swap" rel="stylesheet">
<style>
  :root {
    --page: #ffffff;
    --paper: #efe9d8;
    --glass-light: #e6dfc6;
    --glass-mid: #d6cda4;
    --crimson: #c4134f;
    --bark: #4e2a1c;
    --olive-ink: #7d6c3c;
    --leaf: #7a5038;
    --rose-tone: #b8455e;
  }
  * { margin: 0; padding: 0; box-sizing: border-box; }
  html, body {
    width: 1200px;
    height: 3086px;
    overflow: hidden;
    background: var(--page);
  }
  .label {
    position: absolute;
    left: 10px;
    top: 113px;
    width: 1180px;
    height: 2860px;
    background: var(--paper);
    overflow: hidden;
  }
  .art { position: absolute; }
  .art--glass {
    left: 550px;
    top: 0;
    width: 630px;
    height: 2480px;
    background: linear-gradient(180deg, var(--glass-light) 0%, var(--glass-mid) 50%, var(--glass-light) 100%);
  }
  .art--rose-cluster {
    left: 0;
    top: 230px;
    width: 780px;
    height: 830px;
    background: linear-gradient(135deg, var(--leaf) 0%, var(--rose-tone) 100%);
  }
  .art--leaf {
    left: 390px;
    top: 1955px;
    width: 100px;
    height: 110px;
    background: var(--leaf);
  }
  .art--rose-corner {
    left: 875px;
    top: 2275px;
    width: 305px;
    height: 400px;
    background: linear-gradient(135deg, var(--leaf) 0%, var(--rose-tone) 100%);
  }
  .art--rose-small {
    left: 325px;
    top: 2630px;
    width: 230px;
    height: 155px;
    background: var(--rose-tone);
  }
  .brand-name {
    position: absolute;
    left: 70px;
    top: 1290px;
    font-family: "Playfair Display", "Times New Roman", serif;
    font-weight: 400;
    font-size: 230px;
    line-height: 1;
    letter-spacing: -2px;
    color: var(--crimson);
  }
  .varietal {
    position: absolute;
    left: 140px;
    top: 1560px;
    font-family: "Parisienne", cursive;
    font-size: 200px;
    line-height: 1;
    color: var(--olive-ink);
  }
  .vintage {
    position: absolute;
    left: 90px;
    top: 2270px;
    font-family: "Playfair Display", "Times New Roman", serif;
    font-size: 230px;
    line-height: 1;
    color: var(--crimson);
  }
  .rule {
    position: absolute;
    left: 75px;
    top: 2500px;
    width: 790px;
    height: 4px;
    background: var(--bark);
  }
  .region {
    position: absolute;
    left: 280px;
    top: 2515px;
    font-family: "Parisienne", cursive;
    font-size: 66px;
    line-height: 1;
    color: var(--crimson);
  }
  .abv {
    position: absolute;
    left: 580px;
    top: 2640px;
    font-family: "Playfair Display", "Times New Roman", serif;
    font-size: 74px;
    line-height: 1;
    color: var(--bark);
  }
</style>
</head>
<body>
  <main class="label">
    <div class="art art--glass" role="img" aria-label="Large stylised wine glass illustration in pale olive"></div>
    <div class="art art--rose-cluster" role="img" aria-label="Crimson rose with brown leaves illustration"></div>
    <h1 class="brand-name">Plumvale</h1>
    <p class="varietal">Cabernet</p>
    <div class="art art--leaf" role="img" aria-label="Small falling brown leaf illustration"></div>
    <p class="vintage">2011</p>
    <div class="rule"></div>
    <p class="region">California</p>
    <div class="art art--rose-corner" role="img" aria-label="Crimson rose with leaf illustration"></div>
    <div class="art art--rose-small" role="img" aria-label="Small crimson rose illustration"></div>
    <p class="abv">13.2%</p>
  </main>
</body>
</html>
```